Business Card Design Project

I require a business card with the following information on them for various different people;
name
m:
f:
e:
I have a logo already and will attached that. We are in the construction industry. I require something clean and simple but eye catching at the same time. You can use another colour with our logo if you like and you can style the logo as well if you wish. I am open.
Also it needs to be front and back design.
Industry/Entity Type
Construction
Requirements
Must have
- Logo, name, mobile, fax and email address.
Front and back design

```html
<!DOCTYPE html>
<html lang="en">
<head>
<meta charset="utf-8">
<title>Northvale Builders – Business Card</title>
<link rel="stylesheet" href="https://fonts.googleapis.com/css2?family=Source+Sans+3:wght@400;600;700&display=swap">
<style>
  :root {
    --backdrop: #a8801f;
    --card-white: #ffffff;
    --brand-green: #5cb02c;
    --brand-green-light: #b6dd5e;
    --brand-green-deep: #54a925;
    --ink: #1f1f1f;
    --ink-soft: #3a3a3a;
    --tab-dark: #333333;
  }
  html, body {
    margin: 0;
    padding: 0;
    width: 1200px;
    height: 686px;
    overflow: hidden;
    background: var(--backdrop);
    font-family: "Source Sans 3", sans-serif;
  }
  .canvas {
    position: relative;
    width: 1200px;
    height: 686px;
  }
  .card {
    position: absolute;
    width: 524px;
    height: 298px;
    box-shadow: 2px 3px 4px rgba(0,0,0,0.45);
    overflow: hidden;
  }
  .card--front {
    left: 55px;
    top: 157px;
    background: var(--card-white);
  }
  .card--back {
    left: 612px;
    top: 241px;
    background: radial-gradient(ellipse at 50% 50%, var(--brand-green-light) 0%, #96cc47 45%, var(--brand-green-deep) 100%);
  }
  .side-tab {
    position: absolute;
    top: 124px;
    height: 58px;
    width: 17px;
    display: flex;
  }
  .side-tab--left { left: 0; }
  .side-tab--right { right: 0; flex-direction: row-reverse; }
  .side-tab__green {
    width: 14px;
    background: linear-gradient(180deg, #8fcf4a, var(--brand-green-deep));
  }
  .side-tab__dark {
    width: 3px;
    background: var(--tab-dark);
  }
  .wordmark {
    position: absolute;
    left: 0;
    right: 0;
    display: flex;
    align-items: center;
    justify-content: center;
    gap: 12px;
    font-weight: 400;
    white-space: nowrap;
  }
  .wordmark__square {
    background: var(--brand-green);
  }
  .card--front .wordmark {
    top: 90px;
    font-size: 44px;
    color: var(--ink-soft);
  }
  .card--front .wordmark__square {
    width: 40px;
    height: 40px;
  }
  .card--back .wordmark {
    top: 118px;
    font-size: 56px;
    color: var(--ink);
  }
  .divider {
    position: absolute;
    left: 192px;
    top: 163px;
    width: 126px;
    height: 1px;
    background: linear-gradient(90deg, rgba(0,0,0,0), #222 50%, rgba(0,0,0,0));
  }
  .contact {
    position: absolute;
    left: 0;
    right: 0;
    top: 184px;
    text-align: center;
    color: var(--ink);
    font-size: 13px;
    line-height: 19px;
  }
  .contact__name {
    color: var(--brand-green);
    font-weight: 700;
    font-size: 15.5px;
    margin-bottom: 2px;
  }
  .contact__row {
    display: flex;
    justify-content: center;
    gap: 16px;
  }
  .contact__item {
    display: inline-flex;
    align-items: center;
    gap: 2px;
  }
  .contact__icon {
    width: 12px;
    height: 10px;
    fill: var(--brand-green);
  }
</style>
</head>
<body>
<div class="canvas">

  <section class="card card--front" aria-label="Card front">
    <div class="side-tab side-tab--left"><span class="side-tab__green"></span><span class="side-tab__dark"></span></div>
    <div class="side-tab side-tab--right"><span class="side-tab__green"></span><span class="side-tab__dark"></span></div>

    <div class="wordmark">
      <span class="wordmark__square"></span>
      <span class="wordmark__name">Northvale Builders</span>
    </div>

    <div class="divider"></div>

    <div class="contact">
      <div class="contact__name">Your Name</div>
      <div class="contact__row">
        <span class="contact__item">
          <svg class="contact__icon" viewBox="0 0 12 10" aria-hidden="true"><path d="M1 7c2-4 6-6 10-5l-1 2-2-.5c-1 .6-2 1.6-3 3l1 1.5-2 1C2.5 9 1.5 8.3 1 7z"/></svg>
          123-456-7890
        </span>
        <span class="contact__item">
          <svg class="contact__icon" viewBox="0 0 12 10" aria-hidden="true"><rect x="3" y="0" width="6" height="3"/><rect x="1" y="3.5" width="10" height="4.5"/><rect x="2.5" y="8.5" width="7" height="1.5"/></svg>
          123-456-7890
        </span>
      </div>
      <div class="contact__row">
        <span class="contact__item">
          <svg class="contact__icon" viewBox="0 0 12 10" aria-hidden="true"><rect x="0.5" y="1.5" width="11" height="7.5"/><path d="M0.5 1.5L6 6l5.5-4.5" fill="none" stroke="#fff" stroke-width="1"/></svg>
          name@website.com
        </span>
      </div>
    </div>
  </section>

  <section class="card card--back" aria-label="Card back">
    <div class="wordmark">
      <span class="wordmark__name">Northvale Builders</span>
    </div>
  </section>

</div>
</body>
</html>
```